Business Card for Graphic Design Firm

This project is for a new graphic design firm based in New Jersey called Velmoria. We outsource graphic design and marketing jobs. We want to communicate that this is a professional company but it as well creative and artistic. This card may be used as a horizontal double sided paper card or a vertical single sided translucent card so feel free to submit designs in whichever format or both.
Updates

Reason: Extending the deadline because I'm not exactly satisfied with the designs so far.

Please view the updated project brief

Target Market(s)

Adults aged 25-60

Industry/Entity Type

Graphic Design

Font styles to use
Serif
Sans Serif

Requirements
Nice to have
• Maybe a triangular pattern around the edges similar to our logo

```html
<!DOCTYPE html>
<html lang="en">
<head>
<meta charset="utf-8">
<title>Velmoria Business Card</title>
<link href="https://fonts.googleapis.com/css2?family=Open+Sans:wght@400;600;700&display=swap" rel="stylesheet">
<style>
  :root {
    --page: #e9e6e1;
    --card-top: #2e2e31;
    --card-bottom: #19191b;
    --name-grey: #a9abae;
    --text-light: #f2f2f2;
    --accent-yellow: #f6b417;
    --accent-orange: #f39a2b;
    --teal: #18a3b8;
    --teal-dark: #0e8fa3;
    --white: #ffffff;
  }
  * { margin: 0; padding: 0; box-sizing: border-box; }
  html, body { width: 1200px; height: 1023px; overflow: hidden; }
  body {
    background: var(--page);
    font-family: "Open Sans", Arial, sans-serif;
    position: relative;
  }
  .card {
    position: absolute;
    left: 250px;
    width: 700px;
    height: 400px;
    background: linear-gradient(160deg, var(--card-top), var(--card-bottom));
    border-radius: 4px;
    overflow: hidden;
    box-shadow: 0 6px 18px rgba(0,0,0,0.25);
  }
  .card--front { top: 62px; }
  .card--back { top: 560px; }
  .card__shapes { position: absolute; inset: 0; width: 100%; height: 100%; }

  .brand {
    position: absolute;
    display: flex;
    align-items: center;
    gap: 14px;
    color: var(--name-grey);
    font-weight: 600;
    text-transform: uppercase;
    letter-spacing: 4px;
  }
  .brand__mark { background: var(--name-grey); }
  .card--front .brand { left: 60px; top: 250px; font-size: 34px; }
  .card--front .brand__mark { width: 16px; height: 16px; }
  .card--back .brand { left: 70px; top: 160px; font-size: 52px; }
  .card--back .brand__mark { width: 24px; height: 24px; }

  .divider {
    position: absolute;
    left: 300px; top: 205px;
    width: 90px; height: 2px;
    background: linear-gradient(90deg, transparent, var(--text-light));
  }
  .contact {
    position: absolute;
    right: 80px; top: 70px;
    text-align: right;
    color: var(--text-light);
  }
  .contact__name { font-size: 20px; font-weight: 700; }
  .contact__role { font-size: 14px; color: var(--accent-yellow); margin-bottom: 22px; }
  .contact__line {
    display: flex; justify-content: flex-end; align-items: center; gap: 12px;
    font-size: 14px; margin-bottom: 16px;
  }
  .contact__icon { width: 16px; height: 16px; flex: none; }
  .contact__address { font-size: 14px; line-height: 1.5; margin-right: 28px; }
</style>
</head>
<body>

<section class="card card--front" aria-label="Card front">
  <svg class="card__shapes" viewBox="0 0 700 400" aria-hidden="true">
    <polygon points="700,95 640,120 700,145" fill="var(--accent-orange)"/>
    <polygon points="700,100 650,120 700,140" fill="var(--white)"/>
    <polygon points="0,255 60,280 0,305" fill="var(--accent-orange)"/>
    <polygon points="0,260 50,280 0,300" fill="var(--white)"/>
  </svg>

  <div class="brand"><span class="brand__mark"></span>Velmoria</div>
  <div class="divider"></div>

  <div class="contact">
    <p class="contact__name">Lukas Brenner</p>
    <p class="contact__role">Hybrid Clouds</p>
    <p class="contact__line">+41 70 555 12 34
      <svg class="contact__icon" viewBox="0 0 16 16"><rect x="4" y="1" width="8" height="14" rx="1.5" fill="none" stroke="var(--accent-yellow)" stroke-width="1.6"/><circle cx="8" cy="12.5" r="0.9" fill="var(--accent-yellow)"/></svg>
    </p>
    <p class="contact__line">lukas@velmoria.ch
      <svg class="contact__icon" viewBox="0 0 16 16"><rect x="1" y="3" width="14" height="10" fill="var(--accent-yellow)"/><polyline points="1,3 8,9 15,3" fill="none" stroke="var(--card-bottom)" stroke-width="1.2"/></svg>
    </p>
    <p class="contact__line">&nbsp;
      <svg class="contact__icon" viewBox="0 0 16 16"><polygon points="8,1 15,8 13,8 13,15 3,15 3,8 1,8" fill="var(--accent-yellow)"/><rect x="6.5" y="10" width="3" height="5" fill="var(--card-bottom)"/></svg>
    </p>
    <p class="contact__address">Lindenweg 4b 8000 Talberg<br>Switzerland8000 Talberg, Switzerland</p>
  </div>
</section>

<section class="card card--back" aria-label="Card back">
  <svg class="card__shapes" viewBox="0 0 700 400" aria-hidden="true">
    <polygon points="700,150 700,400 380,400" fill="var(--white)"/>
    <polygon points="700,185 700,400 430,400" fill="var(--teal)"/>
    <polygon points="700,300 700,400 560,400" fill="var(--teal-dark)" opacity="0.5"/>
  </svg>
  <div class="brand"><span class="brand__mark"></span>Velmoria</div>
</section>

</body>
</html>
```